Business Cards - New Logo Rebranding

Hello We know have a red and blue logo and are looking to create new cards. We are looking for the best creativity of the new logo merged with some of the existing artwork provided.

Target Market(s)

Realtors

Industry/Entity Type

Real Estate

Contact Information for Business Card

New logo with rebranded colors

Requirements
Must have
• Creative use of the new logo

```html
<!DOCTYPE html>
<html lang="en">
<head>
<meta charset="utf-8">
<title>Keystone Group – Business Cards</title>
<link href="https://fonts.googleapis.com/css2?family=Arimo:wght@400;700&display=swap" rel="stylesheet">
<style>
  :root {
    --stage: #3e3e3e;
    --card-white: #ffffff;
    --brand-blue: #1565c0;
    --card-blue: #0a6fbd;
    --brand-red: #e0343c;
    --ink: #2b2b2b;
  }
  * { box-sizing: border-box; margin: 0; padding: 0; }
  html, body { width: 1200px; height: 803px; overflow: hidden; }
  body {
    background: var(--stage);
    font-family: "Arimo", Arial, sans-serif;
    position: relative;
  }
  .card {
    position: absolute;
    width: 520px;
    height: 300px;
    border-radius: 22px;
    overflow: hidden;
    box-shadow: 0 14px 30px rgba(0,0,0,.45);
    border-bottom: 4px solid var(--brand-red);
  }
  .card--front { left: 45px; top: 250px; background: var(--card-white); }
  .card--back  { left: 635px; top: 250px; background: var(--card-blue); color: #fff; }

  /* front */
  .front-info { position: absolute; left: 34px; top: 64px; width: 250px; }
  .wordmark {
    font-weight: 700;
    font-size: 25px;
    color: var(--brand-blue);
    letter-spacing: .5px;
    text-transform: uppercase;
    line-height: 1;
  }
  .tagline {
    font-size: 8px;
    font-weight: 700;
    color: var(--brand-blue);
    letter-spacing: .8px;
    margin-top: 4px;
    padding-top: 3px;
    border-top: 2px solid var(--brand-blue);
    display: inline-block;
  }
  .person { margin-top: 30px; }
  .person-name { font-size: 21px; color: var(--brand-blue); font-weight: 400; }
  .person-title { font-size: 13px; color: var(--brand-red); margin-top: 2px; }
  .contacts { list-style: none; margin-top: 18px; }
  .contacts li {
    display: flex; align-items: center; gap: 8px;
    font-size: 12px; color: var(--ink); line-height: 18px;
  }
  .contacts svg { width: 11px; height: 11px; flex: none; }
  .front-mark {
    position: absolute; right: 30px; top: 35px;
    width: 230px; height: 230px;
  }

  /* back */
  .back-mark {
    position: absolute; left: 50%; top: 38px;
    transform: translateX(-50%);
    width: 96px; height: 96px;
  }
  .back-name {
    position: absolute; left: 0; right: 0; top: 150px;
    text-align: center;
  }
  .back-name .wordmark { color: #fff; font-size: 30px; }
  .back-name .tagline { color: #fff; border-color: #fff; font-size: 9px; }
  .services {
    position: absolute; left: 0; right: 0; bottom: 44px;
    text-align: center; font-size: 13px; letter-spacing: .3px;
  }
</style>
</head>
<body>

<section class="card card--front">
  <div class="front-info">
    <div class="wordmark">Keystone Group</div><br>
    <div class="tagline">INSPECTION PROFESSIONALS</div>
    <div class="person">
      <div class="person-name">Dana Morrow</div>
      <div class="person-title">Certified Mold Inspector</div>
    </div>
    <ul class="contacts">
      <li><svg viewBox="0 0 12 12"><path d="M3 1l2 2-1 2c1 1.5 2 2.5 3 3l2-1 2 2-2 2C5 11 1 7 1 3z" fill="var(--brand-blue)"/></svg>800.555.0142</li>
      <li><svg viewBox="0 0 12 12"><rect x="3" y="1" width="6" height="10" rx="1" fill="none" stroke="var(--brand-blue)" stroke-width="1.4"/></svg>562.555.0187</li>
      <li><svg viewBox="0 0 12 12"><rect x="1" y="3" width="10" height="7" fill="var(--brand-blue)"/><path d="M1 3l5 4 5-4" fill="none" stroke="#fff" stroke-width="1"/></svg>dana@keystoneinspect.com</li>
      <li><svg viewBox="0 0 12 12"><circle cx="6" cy="6" r="5" fill="var(--brand-blue)"/></svg>www.KeystoneInspect.com</li>
    </ul>
  </div>
  <svg class="front-mark" viewBox="0 0 230 230" aria-hidden="true">
    <circle cx="115" cy="115" r="108" fill="var(--brand-blue)" stroke="var(--brand-red)" stroke-width="9"/>
  </svg>
</section>

<section class="card card--back">
  <svg class="back-mark" viewBox="0 0 96 96" aria-hidden="true">
    <circle cx="48" cy="48" r="44" fill="none" stroke="#fff" stroke-width="4"/>
  </svg>
  <div class="back-name">
    <div class="wordmark">Keystone Group</div><br>
    <div class="tagline">INSPECTION PROFESSIONALS</div>
  </div>
  <p class="services">HOME • SEWER • MOLD • COMMERCIAL • TERMITE • ROOF</p>
</section>

</body>
</html>
```